10-year customer thank you card

We want a greeting card that our sales reps can send to companies/customers who have been with our company for 10 or more years. We're a software company, our corporate color is blue but we also like green, orange, and purple. We'd like something rather minimal/simplistic for this card, perhaps building off our tree logo. We're really open to ideas for this one. You must use the template files that are uploaded. Copy included in 10 year thank you card file; the copy may change based on how it looks when laid out
Updates

I updated our brief. We'd prefer a sans serif font. I also uploaded a blank infographic image that includes more of our approved colors.

Industry/Entity Type

Software

Font styles to use
Sans Serif

```html
<!DOCTYPE html>
<html lang="en">
<head>
<meta charset="utf-8">
<title>Pinecrest Software – 10 Years Thank You Card</title>
<link rel="stylesheet" href="https://fonts.googleapis.com/css2?family=Raleway:wght@300;400;500&family=Great+Vibes&display=swap">
<style>
  :root {
    --paper: #ffffff;
    --teal: #3fa8b4;
    --teal-deep: #2fb3bf;
    --aqua: #14c9b8;
    --slate: #7f9596;
    --rule: #1e1e1e;
    --ink: #2f3a3c;
    --white: #ffffff;
  }
  html, body {
    margin: 0;
    padding: 0;
    overflow: hidden;
    background: var(--paper);
  }
  .card {
    position: relative;
    width: 870px;
    height: 1200px;
    overflow: hidden;
    background: var(--paper);
    font-family: "Raleway", Arial, sans-serif;
  }

  /* Inside back panel (printed upside down for folding) */
  .back-panel {
    position: absolute;
    left: 0;
    top: 0;
    width: 870px;
    height: 600px;
  }
  .back-panel__bar {
    position: absolute;
    left: 43px;
    top: 0;
    width: 782px;
    height: 11px;
    background: var(--teal);
  }
  .back-panel__rule {
    position: absolute;
    left: 43px;
    top: 75px;
    width: 782px;
    height: 2px;
    background: var(--rule);
  }
  .back-panel__url,
  .back-panel__brand {
    position: absolute;
    top: 34px;
    margin: 0;
    transform: rotate(180deg);
    white-space: nowrap;
  }
  .back-panel__url {
    left: 43px;
    font-size: 19px;
    font-weight: 400;
    color: var(--teal);
    letter-spacing: 0.2px;
  }
  .back-panel__brand {
    right: 43px;
    display: flex;
    align-items: center;
    gap: 8px;
    font-size: 22px;
    font-weight: 500;
    color: var(--ink);
  }
  .brand-square {
    width: 14px;
    height: 14px;
    background: var(--teal);
  }

  /* Front cover */
  .cover {
    position: absolute;
    left: 0;
    top: 600px;
    width: 870px;
    height: 600px;
    background: linear-gradient(180deg, var(--teal) 0%, var(--teal-deep) 55%, var(--teal) 100%);
  }
  .cover__waves {
    position: absolute;
    left: 0;
    top: 262px;
    width: 870px;
    height: 316px;
    background: linear-gradient(175deg,
      rgba(127,149,150,0.55) 0%,
      rgba(20,201,184,0.85) 25%,
      rgba(127,149,150,0.7) 45%,
      rgba(20,201,184,0.6) 62%,
      rgba(127,149,150,0.75) 80%,
      rgba(63,168,180,0.6) 100%);
  }
  .badge {
    position: absolute;
    left: 644px;
    top: 35px;
    width: 181px;
    height: 187px;
    background: var(--slate);
    color: var(--white);
    text-align: center;
  }
  .badge__number {
    display: block;
    margin-top: 4px;
    font-size: 124px;
    font-weight: 300;
    line-height: 1;
    letter-spacing: -4px;
  }
  .badge__label {
    display: block;
    margin-top: -6px;
    font-size: 46px;
    font-weight: 400;
    line-height: 1;
    letter-spacing: -1px;
  }
  .cover__message {
    position: absolute;
    left: 0;
    top: 395px;
    width: 870px;
    margin: 0;
    text-align: center;
    font-family: "Great Vibes", "Brush Script MT", cursive;
    font-weight: 400;
    font-size: 92px;
    line-height: 1;
    color: var(--white);
    text-indent: -10px;
  }
</style>
</head>
<body>
  <main class="card">
    <section class="back-panel">
      <div class="back-panel__bar"></div>
      <p class="back-panel__url">www.pinecrestsoft.com</p>
      <p class="back-panel__brand"><span class="brand-square"></span>Pinecrest Software</p>
      <div class="back-panel__rule"></div>
    </section>

    <section class="cover">
      <div class="cover__waves" role="img" aria-label="Soft flowing waves of aqua and slate grey across the lower cover"></div>
      <div class="badge">
        <span class="badge__number">10</span>
        <span class="badge__label">years</span>
      </div>
      <h1 class="cover__message">Thank You</h1>
    </section>
  </main>
</body>
</html>
```